Im open to ideas.. I was thinking on my business cards aswell as my logo. a place for my name. email. phone number and abn..

ive attched a file with my business logo. which i dont love the colours.. i was think a dark background with charcoal letters so something along those colour schumes but im open to ideas..

BRM Constructions

```html
<!DOCTYPE html>
<html lang="en">
<head>
<meta charset="utf-8">
<title>BRM Constructions – Business Card</title>
<link rel="stylesheet" href="https://fonts.googleapis.com/css2?family=Montserrat:wght@400;500;700&display=swap">
<style>
  :root {
    --page-bg: #d9d4cc;
    --card-top: #2a2a2a;
    --card-mid: #111111;
    --card-bottom: #050505;
    --accent-red: #e8333c;
    --text-white: #f4f4f4;
    --text-grey: #bdbdbd;
    --divider: #6b6b6b;
  }
  * { margin: 0; padding: 0; box-sizing: border-box; }
  html, body {
    width: 1200px;
    height: 1022px;
    overflow: hidden;
  }
  body {
    background: var(--page-bg);
    display: flex;
    align-items: center;
    justify-content: center;
    font-family: "Montserrat", sans-serif;
  }
  .business-card {
    width: 900px;
    height: 514px;
    border-radius: 28px;
    background: linear-gradient(160deg, var(--card-top) 0%, var(--card-mid) 45%, var(--card-bottom) 100%);
    display: flex;
    align-items: center;
    position: relative;
    box-shadow: 0 18px 40px rgba(0,0,0,0.35);
  }
  .brand-panel {
    width: 440px;
    display: flex;
    align-items: center;
    justify-content: center;
    gap: 16px;
  }
  .brand-mark {
    width: 22px;
    height: 22px;
    background: var(--accent-red);
  }
  .brand-name {
    font-weight: 700;
    font-size: 40px;
    letter-spacing: 1px;
    color: var(--text-white);
    text-transform: uppercase;
  }
  .card-divider {
    width: 2px;
    height: 230px;
    background: linear-gradient(to bottom, transparent, var(--divider) 20%, var(--divider) 80%, transparent);
  }
  .contact-panel {
    padding-left: 48px;
    color: var(--text-white);
  }
  .person-name {
    font-weight: 700;
    font-size: 36px;
    color: var(--accent-red);
    text-transform: uppercase;
    letter-spacing: 1px;
  }
  .person-title {
    font-size: 22px;
    margin-top: 4px;
    margin-bottom: 22px;
  }
  .contact-list { list-style: none; }
  .contact-item {
    display: flex;
    align-items: center;
    gap: 12px;
    font-size: 22px;
    line-height: 38px;
  }
  .abn-label {
    color: var(--accent-red);
    font-weight: 700;
  }
  .contact-icon {
    width: 18px;
    height: 18px;
    flex: none;
  }
</style>
</head>
<body>
  <div class="business-card">
    <div class="brand-panel">
      <span class="brand-mark"></span>
      <span class="brand-name">BRM Constructions</span>
    </div>
    <div class="card-divider"></div>
    <div class="contact-panel">
      <p class="person-name">Marcus Hale</p>
      <p class="person-title">Director</p>
      <ul class="contact-list">
        <li class="contact-item"><span><span class="abn-label">ABN</span>: 41 208 665 317</span></li>
        <li class="contact-item">
          <svg class="contact-icon" viewBox="0 0 24 24"><path fill="#e8333c" d="M6.6 10.8a15.1 15.1 0 0 0 6.6 6.6l2.2-2.2a1 1 0 0 1 1-.25 11.4 11.4 0 0 0 3.6.57 1 1 0 0 1 1 1V20a1 1 0 0 1-1 1A17 17 0 0 1 3 4a1 1 0 0 1 1-1h3.5a1 1 0 0 1 1 1c0 1.25.2 2.45.57 3.57a1 1 0 0 1-.25 1z"/></svg>
          <span>+330 2418-7723</span>
        </li>
        <li class="contact-item">
          <svg class="contact-icon" viewBox="0 0 24 24"><rect x="3" y="5" width="18" height="14" rx="2" fill="none" stroke="#e8333c" stroke-width="2"/><path d="M3 7l9 6 9-6" fill="none" stroke="#e8333c" stroke-width="2"/></svg>
          <span>info@brmconstructions.com</span>
        </li>
        <li class="contact-item">
          <svg class="contact-icon" viewBox="0 0 24 24"><circle cx="12" cy="12" r="9" fill="none" stroke="#e8333c" stroke-width="2"/><path d="M3 12h18M12 3c3 3 3 15 0 18M12 3c-3 3-3 15 0 18" fill="none" stroke="#e8333c" stroke-width="1.6"/></svg>
          <span>www.brmconstructions.com</span>
        </li>
      </ul>
    </div>
  </div>
</body>
</html>
```